Hearthside Lending Relief

Please help us give our website a remake or a FACELIFT. It is not very good but it says what we need it to say. But the design is terrible.
I would like our new design font and logo to be used as the theme.

I also want more photos on the site.

I also want consistency with the pages so they look clean.

We want the professionals to do this, let's see what you got!

Thank you!
Updates

Project Deadline Extended
Reason: I can understand you want to be paid. So I will commit to the fee but I want you to have time to make a KICK ASS website for me dudes! Thanks

HI!  Just wanted to say thanks for your time on these.  A lot are great.  However the firefighters have nothing to do with Foreclosure.  We are saving peoples homes from the bank taking them and selling them.   I LOVE the house photos and the families on the website.  That is the direction we like.  THanks.

THANK U ALL FOR THE WORK!   I like a few ending in the numbers: 147  733  693  536  620  478  727  508     I will go over them and choose one soon.  Thank you.   You will be paid shortly. 

Requirements
Must have
• Bright, Upbeat photos. Color scheme should be in order. We like icons on the bottom. not just text.

```html
<!DOCTYPE html>
<html lang="en">
<head>
<meta charset="utf-8">
<title>Hearthside Lending Relief</title>
<link href="https://fonts.googleapis.com/css2?family=Open+Sans:wght@600;700;800&display=swap" rel="stylesheet">
<style>
:root{
  --top-band:#474747;
  --page-grey:#bdbdbd;
  --nav-black:#050505;
  --brand-red:#d82027;
  --red-soft:#e35d63;
  --red-line:#a3141a;
  --accent:#f0222b;
  --white:#ffffff;
  --ink:#0a0a0a;
  --footer-band:#3c3c3c;
  --heading-grey:#8c8c8c;
}
*{margin:0;padding:0;box-sizing:border-box}
html,body{width:1200px;height:1125px;overflow:hidden}
body{
  position:relative;
  font-family:"Open Sans",Arial,sans-serif;
  background:linear-gradient(var(--top-band) 0 375px,var(--page-grey) 375px);
}
.main-nav{
  position:absolute;left:445px;top:0;width:705px;height:70px;
  background:var(--nav-black);border-radius:0 0 12px 12px;
  display:flex;align-items:center;justify-content:center;gap:8px;
  color:var(--white);font-weight:600;font-size:20px;
}
.main-nav a{color:var(--white);text-decoration:none}
.main-nav a.current{color:var(--accent)}
.brand{
  position:absolute;left:56px;top:35px;display:flex;align-items:center;gap:16px;
}
.brand-mark{width:110px;height:110px;border-radius:50%;background:var(--accent)}
.brand-name{
  color:var(--accent);font-weight:800;font-size:25px;line-height:27px;
  text-transform:uppercase;white-space:nowrap;
}
.social{
  position:absolute;left:722px;top:95px;display:flex;gap:26px;align-items:center;
  color:var(--white);font-weight:700;font-size:22px;
}
.photo-strip{
  position:absolute;left:78px;top:165px;width:1038px;height:124px;
  display:flex;gap:14px;
}
.photo-strip .thumb{
  flex:1;border-radius:6px;box-shadow:2px 3px 6px rgba(0,0,0,.45);
}
.thumb.house-day{background:linear-gradient(160deg,#9fd3f2,#f4e3b4 60%,#7cb35b)}
.thumb.family-yard{background:linear-gradient(160deg,#bfe4f7,#f6c99a 55%,#6fae4c)}
.thumb.keys-porch{background:linear-gradient(160deg,#f7e3c0,#d99a62 60%,#8a5a3a)}
.thumb.street-homes{background:linear-gradient(160deg,#a9d8f5,#e9edf2 50%,#86b964)}
.content-panel{
  position:absolute;left:78px;top:309px;width:1038px;height:720px;
  background:var(--red-soft);border-radius:10px 10px 0 0;overflow:hidden;
}
.panel-glow{
  position:absolute;left:-50px;top:-35px;width:1140px;height:790px;
  border-radius:50%;background:var(--brand-red);
}
.panel-header{
  position:absolute;left:0;top:0;width:100%;height:129px;
  border-bottom:3px solid var(--red-line);
  display:flex;align-items:center;padding-left:8px;gap:16px;
}
.home-icon{width:66px;height:66px}
.panel-title{
  font-size:34px;font-weight:800;color:var(--heading-grey);
  text-shadow:2px 2px 2px rgba(0,0,0,.45);
}
.hero-photo{
  position:absolute;left:14px;top:147px;width:382px;height:238px;
  background:linear-gradient(150deg,#a8d9f4,#f3dcae 55%,#78b155);
  box-shadow:3px 4px 6px rgba(0,0,0,.5);
}
.hero-lede{
  position:absolute;left:420px;top:195px;width:570px;text-align:center;
  color:var(--white);font-weight:700;font-size:21px;line-height:45px;
}
.hero-lede .name{color:var(--ink);font-size:18px;display:block;line-height:36px}
.intro-copy{
  position:absolute;left:40px;top:425px;width:960px;text-align:center;
  color:var(--white);font-weight:700;font-size:15.5px;line-height:33px;
  white-space:nowrap;
}
.intro-copy .name{color:var(--ink)}
.intro-copy .larger{font-size:17.5px}
.site-footer{
  position:absolute;left:0;top:1015px;width:1200px;height:110px;
  background:var(--footer-band);border-radius:14px 14px 0 0;
  border-top:2px solid #222;
}
.footer-links{
  position:absolute;left:75px;top:0;width:690px;height:83px;
  background:var(--nav-black);border-radius:0 0 10px 10px;
  display:flex;align-items:center;justify-content:center;gap:18px;
  color:var(--white);font-weight:600;font-size:16px;
}
.footer-links .item{display:flex;align-items:center;gap:6px;white-space:nowrap}
.footer-links svg{width:18px;height:18px;fill:var(--accent)}
</style>
</head>
<body>
<nav class="main-nav">
  <a class="current" href="#">Home Page</a>|<a href="#">About Us</a>|<a href="#">Services</a>|<a href="#">Contact Us</a>|<a href="#">Financing Options</a>
</nav>

<div class="brand">
  <span class="brand-mark"></span>
  <span class="brand-name">Hearthside<br>Lending<br>Relief</span>
</div>

<div class="social">
  <span>Linkside</span>
  <span>Chirpline</span>
  <span>Clipstream</span>
</div>

<div class="photo-strip">
  <div class="thumb house-day" role="img" aria-label="Photo of a bright suburban house on a sunny day"></div>
  <div class="thumb family-yard" role="img" aria-label="Photo of a smiling family in their front yard"></div>
  <div class="thumb keys-porch" role="img" aria-label="Photo of house keys handed over on a porch"></div>
  <div class="thumb street-homes" role="img" aria-label="Photo of a friendly neighbourhood street of homes"></div>
</div>

<main class="content-panel">
  <div class="panel-glow"></div>
  <header class="panel-header">
    <svg class="home-icon" viewBox="0 0 66 66">
      <circle cx="33" cy="33" r="31" fill="#f2f2f2" stroke="#8a1a1a" stroke-width="3"/>
      <path d="M14 34 L33 16 L52 34 Z" fill="#b51c22"/>
      <rect x="20" y="33" width="26" height="18" fill="#b51c22"/>
      <rect x="29" y="39" width="8" height="12" fill="#f2f2f2"/>
    </svg>
    <h1 class="panel-title">Forum</h1>
  </header>

  <div class="hero-photo" role="img" aria-label="Photo of a happy family standing in front of their home"></div>

  <p class="hero-lede">
    <span class="name">HEARTHSIDE LENDING RELIEF</span>
    specializes in assisting homeowners who are in<br>FORECLOSURE,
  </p>

  <p class="intro-copy">
    <span class="name">HEARTHSIDE LENDING RELIEF</span> specializes in assisting homeowners who are in FORECLOSURE, by offering solid<br>
    alternatives to losing your home in a Trustee Sale.&nbsp; Having your home foreclosed on can damage your credit for<br>
    up to 7 years.&nbsp; Most foreclosures end with the home owner being evicted from their home, leaving them with no<br>
    money, no place to live and without ample time to safely remove their possessions from their home.&nbsp; There is no<br>
    need to have this happen to you.&nbsp; No matter what part of foreclosure process you are in, WE CAN HELP!<br>
    If you have received a Notice of Default (NOD) or Notice of Trustee Sale (NTS), you have options.&nbsp; <span class="larger">Contact us</span><br>
    <span class="larger">today</span> to speak to one of our licensed specialist, and let us help you put this situation behind you.
  </p>
</main>

<footer class="site-footer">
  <nav class="footer-links">
    <span class="item"><svg viewBox="0 0 24 24"><path d="M6.6 10.8a15 15 0 0 0 6.6 6.6l2.2-2.2a1 1 0 0 1 1-.25 11 11 0 0 0 3.6.6 1 1 0 0 1 1 1V20a1 1 0 0 1-1 1A17 17 0 0 1 3 4a1 1 0 0 1 1-1h3.5a1 1 0 0 1 1 1c0 1.25.2 2.45.6 3.6a1 1 0 0 1-.25 1z"/></svg>Contact Us</span>
    <span class="item"><svg viewBox="0 0 24 24"><path d="M12 3 2 12h3v9h5v-6h4v6h5v-9h3z"/></svg>Hearthside Lending Relief</span>
    <span class="item"><svg viewBox="0 0 24 24"><path d="M3 5h7l2 2h9v12H3z"/></svg>Archive</span>
    <span class="item"><svg viewBox="0 0 24 24"><path d="M7 10V7a5 5 0 0 1 10 0v3h2v11H5V10zm2 0h6V7a3 3 0 0 0-6 0z"/></svg>Privacy Policy</span>
    <span class="item"><svg viewBox="0 0 24 24"><path d="M12 4 4 13h5v7h6v-7h5z"/></svg>Top</span>
  </nav>
</footer>
</body>
</html>
```